Meridian Tidewren Pale Ale Beer Label/Badge

We need a Beer Label designed for our first official beer to be launched under The meridian Brand!!
It will be a Pale Ale Called "Tidewren Pale Ale"!

The Meridian has the largest Craft Beer & Cider selection in the Geelong & Surf Coast region. With a funky location and a relaxed vibe, Meridian prides itself on serving delicious, unique seasonal food paired with Australia's best Craft Beer. The meridian is the perfect setting for a relaxed afternoon or evening with friends and can package an experience for larger groups or corporate bookings.

The Meridian Tavern brand has been growing for over a year and a half and the first label needs to integrate The meridian Logo but at the same time bring a fresh, new and eye catching feel to it along with embracing the "Odysseus" story in which we will be naming future beers.

The story of Tidewren is found via the following link
http://lorevault.example/wiki/Tidewren_(folklore)

We expect designers to research The meridian Tavern brand along with the all important Craft Beer Market and demographics. This will, potentially, be the start of many more labels to come for the winning designer!!

Requirements
Must have
• The original "O" needs to be integrated into the new logo and as much as the Greek mythology is being used it needs to be certain that this is an original Australian Craft Beer in the modern age!!
strong, modern & unique!!
Nice to have
• Logo could have a depiction of Tidewren
Should not have
• tackiness or cheap!!

```html
<!DOCTYPE html>
<html lang="en">
<head>
<meta charset="utf-8">
<title>Meridian Tidewren Pale Ale Label</title>
<link rel="stylesheet" href="https://fonts.googleapis.com/css2?family=Saira:wght@600&family=Josefin+Sans:wght@200;400&family=Sarpanch:wght@800&display=swap">
<style>
  :root {
    --page: #ffffff;
    --label: #2b282a;
    --panel: #3e3b3e;
    --ink-light: #ebe8ea;
    --cap-red: #8a2a24;
    --ale-pink: #ec8a8a;
    --figure-light: #f4f2f2;
    --figure-mid: #d9d5d6;
  }
  * { margin: 0; padding: 0; box-sizing: border-box; }
  html, body { width: 747px; height: 1200px; overflow: hidden; background: var(--page); }
  .canvas { position: relative; width: 747px; height: 1200px; }
  .label-shape { position: absolute; left: 0; top: 0; }
  .brand-name {
    position: absolute; left: 0; width: 741px; top: 158px;
    text-align: center; color: var(--ink-light);
    font-family: "Saira", sans-serif; font-weight: 600; font-size: 72px;
    letter-spacing: 6px; line-height: 1;
  }
  .brand-sub {
    position: absolute; left: 0; width: 741px; top: 245px;
    text-align: center; color: var(--ink-light);
    font-family: "Josefin Sans", sans-serif; font-weight: 400; font-size: 27px;
    letter-spacing: 4px; line-height: 1;
  }
  .brand-seal {
    position: absolute; left: 294px; top: 296px; width: 150px; height: 150px;
    border-radius: 50%; background: var(--cap-red);
  }
  .figure-emblem {
    position: absolute; left: 286px; top: 555px; width: 160px; height: 225px;
    background: radial-gradient(ellipse at 50% 35%, var(--figure-light) 0%, var(--figure-mid) 75%);
    border-radius: 80px 80px 10px 10px;
  }
  .beer-name {
    position: absolute; left: 0; width: 741px; top: 800px;
    text-align: center; color: #ffffff;
    font-family: "Sarpanch", sans-serif; font-weight: 800; font-size: 84px;
    letter-spacing: 2px; line-height: 1.1;
  }
  .beer-style {
    position: absolute; left: 0; width: 741px; top: 916px;
    text-align: center; color: var(--ale-pink);
    font-family: "Josefin Sans", sans-serif; font-weight: 200; font-size: 84px;
    letter-spacing: 3px; line-height: 1;
  }
</style>
</head>
<body>
<main class="canvas">
  <svg class="label-shape" width="747" height="1200" viewBox="0 0 747 1200" aria-hidden="true">
    <rect x="96" y="130" width="549" height="916" rx="3" fill="var(--label)"/>
    <path d="M130 130 H604 Q612 130 612 138 V236 L378 512 Q373 518 368 512 L122 236 V138 Q122 130 130 130 Z" fill="var(--panel)"/>
    <path d="M368 526 Q373 520 378 526 L612 712 V900 Q612 908 604 908 H130 Q122 908 122 900 V712 Z" fill="var(--panel)"/>
  </svg>

  <h1 class="brand-name">MERIDIAN</h1>
  <p class="brand-sub">TAVERN + BREWERY</p>
  <div class="brand-seal" aria-hidden="true"></div>

  <div class="figure-emblem" role="img" aria-label="Emblem of a helmeted Greek figure within a laurel wreath atop an Ionic column capital"></div>

  <h2 class="beer-name">TIDEWREN</h2>
  <p class="beer-style">PALE ALE</p>
</main>
</body>
</html>
```